QRV Advisors needs a web site

We need a web site for www.qrvadvisors-example.com. QRV is a mergers and acquisition consulting company that focuses our buyer and seller services on logistics companies. We help put companies together, and help with legal and financial due diligence. We want the web site to express our service and show the logistics components. We want personalized images versus pictures of trucks and airplanes.

Our new logo uses Burgandy and grey colors. Image attached. We are not in to bold, big letters...classy, artistic, low key preferred. Confidentiality, experience, professional are what we want to express on the site.

All we expect for the first part of this project is a home page, and one subpage.  We are budgeting other funds for the technical aspects of the web site

Reason: All that I'm seeing so far is trucks, forklifts and planes. We are a legal mergers and acquisitions firm that focus on logistics. I like some of the images to say logistics, but really want it say legal, financial, and putting companies together. Will pay extra for the sub page if someone can impress us with a home page.

Reason: Swamped with another project at the moment...will work on this over the weekend and provide designer feedback and select final design by Tuesday

```html
<!DOCTYPE html>
<html lang="en">
<head>
<meta charset="utf-8">
<title>QRV Advisors — Home</title>
<link href="https://fonts.googleapis.com/css2?family=Lato:wght@400;700&family=Ubuntu:wght@400;500;700&display=swap" rel="stylesheet">
<style>
:root{
  --burgundy:#a30034;
  --burgundy-dark:#8c002c;
  --charcoal:#333333;
  --nav:#3a3a3a;
  --grey-text:#555;
  --panel:#f4f3f3;
  --panel-line:#dcdcdc;
  --light:#f2f2f2;
  --white:#fff;
}
*{box-sizing:border-box;margin:0;padding:0}
html,body{width:1174px;height:1200px;overflow:hidden;background:#fff}
body{font-family:"Lato",sans-serif;color:var(--charcoal)}
.page{position:relative;width:1174px;height:1200px;overflow:hidden;background:#fff}
.abs{position:absolute}

/* header */
.header{left:0;top:0;width:1174px;height:103px;background:linear-gradient(#fdfdfd,#ececec)}
.brand{left:121px;top:22px;display:flex;align-items:center;height:66px}
.brand-mark{font-family:"Ubuntu",sans-serif;font-weight:500;font-size:64px;letter-spacing:6px;color:#3c3c3c;line-height:1}
.brand-rule{width:2px;height:66px;background:#555;margin:0 14px 0 18px}
.brand-name{font-family:"Ubuntu",sans-serif;font-weight:500;font-size:22px;line-height:24px;color:#555;letter-spacing:1px}
.phone{right:52px;top:38px;display:flex;align-items:center;gap:14px;font-family:"Ubuntu",sans-serif;font-size:23px;color:var(--burgundy)}

/* nav */
.nav{left:0;top:103px;width:1174px;height:50px;background:var(--nav)}
.nav ul{list-style:none;position:absolute;left:124px;top:0;display:flex;height:50px}
.nav li{height:50px;line-height:50px;font-family:"Ubuntu",sans-serif;font-size:18px;color:#fff;padding:0 10px;border-right:1px solid #262626}
.nav li:last-child{border-right:none}
.nav li.active{background:#fff;color:var(--burgundy);width:89px;text-align:center}
.search{left:828px;top:9px;width:214px;height:28px;background:#a9a9a9;border-radius:2px;color:#fff;font-size:13px;padding:6px 10px}
.search svg{position:absolute;right:7px;top:6px}

/* hero */
.hero{left:0;top:153px;width:1174px;height:336px;background:linear-gradient(90deg,#d8c8bc 0%,#e8e8ec 30%,#cfd6e0 50%,#ebe3d8 75%,#f0e6d6 100%)}
.hero-caption{left:0;top:442px;width:1174px;height:47px;background:rgba(20,20,20,.82)}
.hero-caption p{position:absolute;left:131px;top:10px;font-size:22px;color:#fff;font-family:"Lato",sans-serif}
.dots{left:957px;top:459px;display:flex;gap:9px}
.dots span{width:11px;height:11px;border-radius:50%;background:#eee}
.dots span.on{background:var(--burgundy)}

/* service tabs */
.services{left:326px;top:483px;width:522px;height:83px;background:linear-gradient(#fafafa,#e8e8e8);border-radius:6px;box-shadow:0 3px 6px rgba(0,0,0,.25)}
.service{position:absolute;top:0;height:83px;display:flex;align-items:center}
.service .label{font-family:"Ubuntu",sans-serif;font-size:22px;color:var(--burgundy);letter-spacing:.5px}
.services .divider{position:absolute;left:220px;top:12px;width:1px;height:60px;background:#cfcfcf}

/* panels */
.panel{top:615px;width:296px;height:298px;background:var(--panel);border:1px solid var(--panel-line)}
.panel-tab{position:absolute;top:-6px;left:54px;width:186px;height:30px;background:var(--burgundy);color:#fff;font-family:"Ubuntu",sans-serif;font-weight:500;font-size:17px;text-align:center;line-height:30px;border-radius:0 0 4px 4px}
.btn{position:absolute;height:20px;background:#333;color:#fff;font-size:12.5px;font-weight:700;line-height:20px;text-align:center;border-radius:5px 5px 0 0}
.mission-photo{position:absolute;left:11px;top:46px;width:268px;height:94px;border:4px solid #fff;outline:1px solid #ddd;background:linear-gradient(90deg,#7a6a5e,#c9b4a0 30%,#e6d6c3 50%,#b39c88 70%,#6a5e58)}
.mission-text{position:absolute;left:16px;top:156px;width:270px;font-size:12.6px;line-height:18.2px;color:#444}

.news-item{position:absolute;left:14px;width:270px}
.date{position:absolute;left:0;top:0;width:34px;height:41px;background:#d8d8d8;text-align:center;border-radius:2px}
.date .m{display:block;background:#333;color:#fff;font-size:11.5px;line-height:16px}
.date .d{display:block;font-family:"Ubuntu",sans-serif;font-size:17px;color:#333;line-height:24px;letter-spacing:1px}
.news-body{position:absolute;left:52px;top:-4px;width:230px}
.news-body h4{font-size:13.5px;font-weight:700;color:#333;line-height:18px;font-weight:400}
.news-body p{font-size:12.5px;line-height:16.5px;color:#444}
.news-rule{position:absolute;left:14px;width:270px;height:1px;background:#d6d6d6}

.form-row{position:absolute;left:19px;font-size:13.5px;color:#444}
.field{position:absolute;left:85px;width:187px;height:22px;background:#fff;border:1px solid #cfcfcf}

/* partners */
.partners{left:0;top:941px;width:1174px;height:84px}
.partner{position:absolute;top:26px;display:flex;align-items:center;gap:8px;font-family:"Ubuntu",sans-serif;font-weight:700;font-size:25px;color:#1b5f9e}
.partner i{display:block;width:18px;height:18px;border-radius:50%;background:#1b5f9e}
.partner.p2{color:#1d3c53}.partner.p2 i{background:#1d3c53}
.partner.p3{color:#1b3f7e}.partner.p3 i{background:#f2c00f;border-radius:0}
.partner.p4{color:#666;font-weight:400}.partner.p4 i{background:#26a7d9}

/* footer */
.footer{left:0;top:1033px;width:1174px;height:167px;background:var(--burgundy);color:#fff}
.footer h3{position:absolute;top:12px;font-family:"Ubuntu",sans-serif;font-weight:400;font-size:18.5px}
.quick{position:absolute;left:137px;top:53px;list-style:none}
.quick li{font-size:13.5px;font-weight:700;line-height:19.6px}
.newsletter p{position:absolute;left:337px;top:47px;width:260px;font-size:12.5px;line-height:16px}
.email{position:absolute;left:335px;top:86px;width:200px;height:23px;background:#fff;border-radius:2px;color:#888;font-size:12.5px;padding:3px 9px}
.subscribe{position:absolute;left:335px;top:124px;width:80px;height:22px;background:#333;border-radius:3px;font-family:"Ubuntu",sans-serif;font-weight:500;font-size:14px;text-align:center;line-height:22px}
.social{position:absolute;left:637px;display:flex;align-items:center;gap:13px;font-size:14px;font-weight:700}
.social i{display:block;width:26px;height:26px;border-radius:4px;background:#f3f3f3}
.footer-brand{position:absolute;left:816px;top:26px;width:217px;text-align:center;font-family:"Ubuntu",sans-serif;font-weight:500;font-size:74px;letter-spacing:14px;line-height:74px}
.copyright{position:absolute;left:826px;top:116px;width:222px;text-align:center;font-size:12.5px;line-height:18px}
</style>
</head>
<body>
<div class="page">

  <header class="header abs">
    <div class="brand abs">
      <span class="brand-mark">QRV</span>
      <span class="brand-rule"></span>
      <span class="brand-name">QRV<br>ADVISORS</span>
    </div>
    <div class="phone abs">
      <svg width="26" height="26" viewBox="0 0 26 26" aria-hidden="true"><circle cx="13" cy="13" r="11.5" fill="none" stroke="#666" stroke-width="1.6"/><path d="M9.5 7.5c-1.3.8-1.8 2.4-1 4.3 1.2 2.8 3.6 5.2 6.3 6.4 1.8.8 3.3.3 4.1-1l-2.3-2-1.4 1c-1.5-.7-2.7-2-3.4-3.4l1-1.4z" fill="#666"/></svg>
      <span>123 456 7890</span>
    </div>
  </header>

  <nav class="nav abs">
    <ul>
      <li class="active">Home</li>
      <li>About Us</li>
      <li>Consulting Services</li>
      <li>News &amp; Events</li>
      <li>FAQ's</li>
      <li>Contact Us</li>
    </ul>
    <div class="search abs">Search
      <svg width="16" height="16" viewBox="0 0 16 16" aria-hidden="true"><circle cx="6.5" cy="6.5" r="4.5" fill="none" stroke="#fff" stroke-width="2"/><path d="M10 10l4.5 4.5" stroke="#fff" stroke-width="2.4"/></svg>
    </div>
  </nav>

  <div class="hero abs" role="img" aria-label="Photo of two business professionals smiling at each other in a bright office"></div>
  <div class="hero-caption abs"><p>QRV Services Are Offered By Industry Executives With Extensive M&amp;A Experience</p></div>
  <div class="dots abs"><span class="on"></span><span></span><span></span><span></span><span></span></div>

  <section class="services abs">
    <div class="service" style="left:14px">
      <svg width="50" height="76" viewBox="0 0 50 76" aria-hidden="true"><path d="M25 4L9 30h10v14L4 72h13l8-16 8 16h13L31 44V30h10z" fill="#555"/></svg>
      <span class="label" style="margin-left:12px">Mergers</span>
      <svg style="margin-left:27px" width="24" height="24" viewBox="0 0 24 24" aria-hidden="true"><circle cx="12" cy="12" r="10" fill="none" stroke="#555" stroke-width="2"/><path d="M6.5 10.5h6v-3l5 4.5-5 4.5v-3h-6z" fill="#555"/></svg>
    </div>
    <span class="divider"></span>
    <div class="service" style="left:242px">
      <svg width="92" height="40" viewBox="0 0 92 40" aria-hidden="true"><path d="M0 20L24 2v11h44V2l24 18-24 18V27H24v11z" fill="#555"/></svg>
      <span class="label" style="margin-left:14px">Acquisition</span>
      <svg style="margin-left:26px" width="24" height="24" viewBox="0 0 24 24" aria-hidden="true"><circle cx="12" cy="12" r="10" fill="none" stroke="#555" stroke-width="2"/><path d="M6.5 10.5h6v-3l5 4.5-5 4.5v-3h-6z" fill="#555"/></svg>
    </div>
  </section>

  <section class="panel abs" style="left:121px">
    <div class="panel-tab">Our Mission</div>
    <div class="mission-photo" role="img" aria-label="Group photo of a diverse professional team"></div>
    <p class="mission-text">Lorem Ipsum is simply dummy text of the printing and typesetting industry. Lorem Ipsum has been the industry's standard dummy text ever since the 1500sstandard dummy text ever since the 1500s dustry. Lorem Idustry. Lorem I dustry. Lorem.,</p>
    <span class="btn" style="left:203px;top:278px;width:78px">Read More</span>
  </section>

  <section class="panel abs" style="left:440px">
    <div class="panel-tab">News &amp; Events</div>
    <div class="news-item" style="top:42px">
      <div class="date"><span class="m">APR</span><span class="d">02</span></div>
      <div class="news-body"><h4>Lorem ipsum dolor sit amet</h4><p>Lorem ipsum dol adipiscing elit, seder or sit amet, consectetu industry's standard dummy text ever er</p></div>
    </div>
    <span class="news-rule" style="top:118px"></span>
    <div class="news-item" style="top:129px">
      <div class="date"><span class="m">APR</span><span class="d">02</span></div>
      <div class="news-body"><h4>Lorem ipsum dolor sit amet</h4><p>Lorem ipsum dol adipiscing elit, seder or sit amet, consectetu industry's standard dummy text ever er</p></div>
    </div>
    <span class="news-rule" style="top:208px"></span>
    <div class="news-item" style="top:218px">
      <div class="date"><span class="m">APR</span><span class="d">02</span></div>
      <div class="news-body"><h4>Lorem ipsum dolor sit amet</h4><p>Lorem ipsum dol adipiscing elit, seder or sit amet, consectetu</p></div>
    </div>
    <span class="btn" style="left:202px;top:278px;width:76px">Read More</span>
  </section>

  <section class="panel abs" style="left:758px">
    <div class="panel-tab">Get in touch</div>
    <span class="form-row" style="top:47px">Name</span><span class="field" style="top:43px"></span>
    <span class="form-row" style="top:92px">Phone</span><span class="field" style="top:88px"></span>
    <span class="form-row" style="top:135px">Email</span><span class="field" style="top:131px"></span>
    <span class="form-row" style="top:180px">Message</span><span class="field" style="top:176px;height:68px"></span>
    <span class="btn" style="left:208px;top:278px;width:66px">Submit</span>
  </section>

  <section class="partners abs">
    <svg class="abs" style="left:136px;top:28px" width="20" height="30" viewBox="0 0 20 30" aria-hidden="true"><path d="M16 3L5 15l11 12" fill="none" stroke="#888" stroke-width="4"/></svg>
    <div class="partner" style="left:224px"><i></i>Meridian</div>
    <div class="partner p2" style="left:430px"><i></i>PortLane</div>
    <div class="partner p3" style="left:628px"><i></i>Swiftway</div>
    <div class="partner p4" style="left:825px"><i></i>CarryShare</div>
    <svg class="abs" style="left:1030px;top:28px" width="20" height="30" viewBox="0 0 20 30" aria-hidden="true"><path d="M4 3l11 12L4 27" fill="none" stroke="#888" stroke-width="4"/></svg>
  </section>

  <footer class="footer abs">
    <h3 style="left:137px">Quick Links</h3>
    <ul class="quick">
      <li>Home</li><li>About Us</li><li>Consulting Services</li><li>News &amp; Events</li><li>FAQ's</li><li>Contact Us</li>
    </ul>
    <h3 style="left:337px">Newsletter</h3>
    <div class="newsletter"><p>Lorem Ipsum is simply dummy text of the printing and typesetting industry.</p></div>
    <div class="email">your e-mail address</div>
    <div class="subscribe">Subscribe</div>
    <h3 style="left:636px">Follow Us</h3>
    <div class="social" style="top:46px"><i></i>Friendpage</div>
    <div class="social" style="top:84px"><i></i>Chirpline</div>
    <div class="social" style="top:119px"><i></i>Workcircle</div>
    <div class="footer-brand">QRV</div>
    <p class="copyright">© 2014 Qrvadvisors.<br>All Rights Reserved</p>
  </footer>

</div>
</body>
</html>
```